1876 Basins & Spouts Business Card

I'm wanting to get a business card designed. Our business is 1876 Basins & Spouts
Details for the card:

1876 Basins & Spouts
Name: Harold Vesk
Email: harold@1876basinsandspouts.com.au
Website: www.1876basinsandspouts.com.au
Mobile: 0438 260 947
Phone: 02 7481 3926

Font of Basins & Spouts is called Snell Roundhand. Not sue what font logo text is.

I'm thinking two sided but it doesn't have to be.

```html
<!DOCTYPE html>
<html lang="en">
<head>
<meta charset="utf-8">
<title>1876 Basins &amp; Spouts – Business Card</title>
<link rel="stylesheet" href="https://fonts.googleapis.com/css2?family=Lato:wght@300;400&family=Montserrat:wght@600&display=swap">
<style>
  :root {
    --stage: #e9e8e6;
    --ink: #231f20;
    --paper: #ffffff;
    --rule: #6d6b6b;
    --muted: #4a4748;
  }
  * { box-sizing: border-box; margin: 0; padding: 0; }
  html, body { width: 1200px; height: 912px; overflow: hidden; }
  body {
    background: var(--stage);
    font-family: "Lato", sans-serif;
    color: var(--ink);
    position: relative;
  }
  .card {
    position: absolute;
    left: 320px;
    width: 560px;
    height: 320px;
    border-radius: 16px;
    overflow: hidden;
    box-shadow: 0 6px 18px rgba(0,0,0,.18);
  }
  /* Back side */
  .card--back { top: 96px; background: var(--ink); display: flex; align-items: center; justify-content: center; }
  .back-name {
    font-family: "Lato", sans-serif;
    font-weight: 300;
    font-size: 34px;
    letter-spacing: 1px;
    color: var(--paper);
  }
  /* Front side */
  .card--front { top: 496px; background: var(--paper); }
  .brand { position: absolute; left: 30px; top: 62px; }
  .brand-name { font-family: "Lato", sans-serif; font-weight: 400; font-size: 21px; color: var(--ink); }
  .brand-tagline { font-size: 8px; color: var(--muted); margin-top: 4px; letter-spacing: .2px; }
  .person { position: absolute; right: 30px; top: 38px; text-align: right; }
  .person-name { font-family: "Montserrat", sans-serif; font-weight: 600; font-size: 19px; letter-spacing: .5px; text-transform: uppercase; }
  .person-role { font-size: 12px; color: var(--muted); margin-top: 1px; }
  .person-rule { position: absolute; right: 30px; top: 86px; width: 230px; height: 1px; background: var(--rule); }
  .address { position: absolute; right: 30px; top: 104px; text-align: right; font-size: 14px; line-height: 1.35; }
  .contact-rule { position: absolute; left: 30px; top: 212px; width: 270px; height: 1px; background: var(--rule); }
  .contacts { position: absolute; left: 34px; top: 222px; list-style: none; }
  .contacts li { display: flex; align-items: center; gap: 8px; font-size: 14px; line-height: 21px; }
  .contacts svg { width: 11px; height: 11px; flex: none; }
  .swoosh { position: absolute; inset: 0; width: 560px; height: 320px; }
</style>
</head>
<body>
  <section class="card card--back" aria-label="Card back">
    <span class="back-name">1876 Basins &amp; Spouts</span>
  </section>

  <section class="card card--front" aria-label="Card front">
    <svg class="swoosh" viewBox="0 0 560 320" aria-hidden="true">
      <path d="M560 190 H440 C418 190 410 200 400 214 L382 240 C374 252 366 256 350 256 H334 V262 H560 Z" fill="var(--ink)"/>
      <path d="M560 270 H356 C346 270 340 274 334 282 L322 298 H560 Z" fill="var(--ink)"/>
      <path d="M300 306 H560 V320 H292 Z" fill="var(--ink)"/>
    </svg>

    <div class="brand">
      <div class="brand-name">1876 Basins &amp; Spouts</div>
      <div class="brand-tagline">Pairing classic elegance with everyday function</div>
    </div>

    <div class="person">
      <div class="person-name">Harold Vesk</div>
      <div class="person-role">Director</div>
    </div>
    <div class="person-rule"></div>
    <div class="address">PO Box 48 Glen<br>Harrow NSW 2793</div>

    <div class="contact-rule"></div>
    <ul class="contacts">
      <li><svg viewBox="0 0 12 12"><path d="M2.5 1 L4.5 1 L5.2 3.6 L4 4.6 C4.7 6 6 7.3 7.4 8 L8.4 6.8 L11 7.5 V9.5 C11 10.4 10.3 11 9.5 11 C5 10.7 1.3 7 1 2.5 C1 1.7 1.6 1 2.5 1 Z" fill="var(--ink)"/></svg>0438 260 947</li>
      <li><svg viewBox="0 0 12 12"><rect x="3" y="0.8" width="6" height="10.4" rx="1" fill="none" stroke="var(--ink)" stroke-width="1.2"/><circle cx="6" cy="9.3" r=".7" fill="var(--ink)"/></svg>02 7481 3926</li>
      <li><svg viewBox="0 0 12 12"><rect x="0.8" y="2.3" width="10.4" height="7.4" fill="none" stroke="var(--ink)" stroke-width="1.1"/><path d="M1 2.6 L6 6.6 L11 2.6" fill="none" stroke="var(--ink)" stroke-width="1.1"/></svg>harold@1876basinsandspouts.com.au</li>
      <li><svg viewBox="0 0 12 12"><circle cx="6" cy="6" r="5.2" fill="var(--ink)"/><path d="M1 6 H11 M6 0.8 C3.6 3.5 3.6 8.5 6 11.2 M6 0.8 C8.4 3.5 8.4 8.5 6 11.2" fill="none" stroke="#fff" stroke-width=".7"/></svg>www.1876basinsandspouts.com.au</li>
    </ul>
  </section>
</body>
</html>
```